KRV Photography Business Card Design

I would like a business card designed in the shape of a camera.
Would like to see various camera designs. Would like to see what the card looks like in different colors. Would like to see which logo looks better on the various camera designs so please show me some with the white logo and some with the black logo. If you need a different file formats please let me know.
Project Deadline Extended Reason: My grandfather passed away and dealing with funeral plans so need to extend deadline. Added Tuesday, March 1, 2016
Project Deadline Extended
Reason: I just got back from out of town. My grandfather's passing was the primary focus for me these past few weeks and the funeral is over so now I will concentrate on picking my business card design. I really appreciate each designer who has taken the time to submit a design. Your effort has not gone unnoticed. I look forward to seeing more amazing designs.
Business
Contact Information for Business Card
Dorine
555-418-2706
https://www.facebook.com/krvphotographyfreelance/
MonaDorine@krv-photography.example

```html
<!DOCTYPE html>
<html lang="en">
<head>
<meta charset="utf-8">
<title>KRV Photography Business Card</title>
<link href="https://fonts.googleapis.com/css2?family=Cinzel:wght@500&family=Roboto:wght@400;700&display=swap" rel="stylesheet">
<style>
  :root {
    --backdrop: #e9e6e2;
    --card-dark: #1f1f1f;
    --card-light: #ffffff;
    --gold: #c99a3e;
    --accent: #b8732a;
    --text: #555555;
    --crop-dark: #8a8a8a;
    --crop-light: #555555;
  }
  * { margin: 0; padding: 0; box-sizing: border-box; }
  html, body { width: 1200px; height: 1000px; overflow: hidden; }
  body { position: relative; background: var(--backdrop); }
  .card {
    position: absolute;
    left: 242px;
    width: 716px;
    height: 410px;
  }
  .card--front { top: 81px; background: var(--card-dark); }
  .card--back { top: 510px; background: var(--card-light); }
  .crop-marks { position: absolute; inset: 0; width: 100%; height: 100%; }
  .card--front .crop-marks { stroke: var(--crop-dark); }
  .card--back .crop-marks { stroke: var(--crop-light); }
  .brand {
    position: absolute;
    left: 0; right: 0; top: 133px;
    display: flex; flex-direction: column; align-items: center;
  }
  .brand__dot {
    width: 92px; height: 92px; border-radius: 50%;
    background: var(--gold);
  }
  .brand__name {
    margin-top: 18px;
    font-family: "Cinzel", serif;
    font-weight: 500;
    font-size: 27px;
    letter-spacing: 0.5px;
    color: var(--gold);
  }
  .contact {
    position: absolute;
    left: 0; right: 0; top: 134px;
    text-align: center;
    font-family: "Roboto", sans-serif;
  }
  .contact__name {
    font-weight: 700;
    font-size: 26px;
    letter-spacing: 1px;
    color: var(--accent);
    margin-bottom: 14px;
  }
  .contact__line {
    font-size: 16.5px;
    line-height: 31.5px;
    color: var(--text);
  }
</style>
</head>
<body>
  <section class="card card--front">
    <svg class="crop-marks" viewBox="0 0 716 410" fill="none" stroke-width="1.5">
      <path d="M34 62 V34 H62"/>
      <path d="M654 34 H682 V62"/>
      <path d="M34 348 V376 H62"/>
      <path d="M654 376 H682 V348"/>
    </svg>
    <div class="brand">
      <div class="brand__dot"></div>
      <div class="brand__name">KRV PHOTOGRAPHY</div>
    </div>
  </section>

  <section class="card card--back">
    <svg class="crop-marks" viewBox="0 0 716 410" fill="none" stroke-width="1.5">
      <path d="M34 62 V34 H62"/>
      <path d="M654 34 H682 V62"/>
      <path d="M34 348 V376 H62"/>
      <path d="M654 376 H682 V348"/>
    </svg>
    <div class="contact">
      <p class="contact__name">DORINE</p>
      <p class="contact__line">555-418-2706</p>
      <p class="contact__line">/krvphotographyfreelance</p>
      <p class="contact__line">MonaDorine@krv-photography.example</p>
    </div>
  </section>
</body>
</html>
```